Lucky Harbour Fun Casino Entertainment

Looking to update my business card and make it look more modern, stand out and eye catching.
We are are fun casino business in Australia (primarily Sydney). Blackjack and Roulette are our most popular games although we have pretty much every game available for hire that you would find in a real casino. The final design would need to be sleek and appeal to the more upmarket corporate sector.
We mainly cater for Corporate Events, Private Parties, Fundraising Events, Team Building, Poker Tournaments
I think I'd prefer the colour Black.

Target Market(s)

High-end Corporate

Industry/Entity Type

Events

Contact Information for Business Card

Rob Kendall
Director
1300 482 617
0433 728 591
info@luckyharbour.com.au
www.luckyharbour.com.au
Facebook & Instagram @luckyharbourevents (proper social icons preferred)

Colors
000000
0255a3

Requirements
Must have
• Front side:
• Logo
• Contact details
• 'Australia's #1 Fun Casino Specialists'
• Back:
• Logo
Nice to have
• Back:
• Corporate Events
• Private Parties
• Poker Tournaments
• Fundraising
• Props & Theming
• Photo Booth
• Horse Racing Events
• The Vegas Sign attached, maybe on the back of the card in the background...?

```html
<!DOCTYPE html>
<html lang="en">
<head>
<meta charset="utf-8">
<title>Lucky Harbour Business Card</title>
<link rel="stylesheet" href="https://fonts.googleapis.com/css2?family=Exo+2:wght@500;600;700;800&display=swap">
<style>
  :root {
    --stage: #2a2c2f;
    --card: #0c0c0d;
    --card-edge: #1b1b1d;
    --gold: #ffc21a;
    --amber: #f7931e;
    --sun: #ffd52a;
    --ink: #0a0a0a;
    --text: #e9e9e9;
    --muted: #bdbdbd;
  }
  * { box-sizing: border-box; margin: 0; padding: 0; }
  html, body {
    width: 1200px; height: 900px; overflow: hidden;
    background: var(--stage);
    font-family: "Exo 2", "Segoe UI", sans-serif;
  }
  .canvas {
    position: relative; width: 1200px; height: 900px;
  }
  .card {
    position: absolute;
    width: 520px; height: 298px;
    border-radius: 22px;
    background: radial-gradient(circle at 30% 25%, #1a1a1c 0%, var(--card) 60%);
    box-shadow: 0 0 0 1px var(--card-edge);
    overflow: hidden;
  }
  .card--front { left: 50px; top: 301px; }
  .card--back  { left: 630px; top: 301px; }

  /* Brand mark */
  .brand {
    position: absolute;
    display: flex; align-items: center; gap: 14px;
  }
  .brand__dot {
    width: 74px; height: 74px; border-radius: 50%;
    background: var(--amber);
    flex: none;
  }
  .brand__name {
    color: var(--gold);
    font-weight: 800;
    font-size: 30px;
    line-height: 1;
    letter-spacing: 1px;
    text-transform: uppercase;
  }
  .card--front .brand { left: 30px; top: 48px; }
  .card--back .brand  { left: 34px; top: 102px; }

  /* Front details */
  .contact {
    position: absolute; left: 278px; top: 40px; width: 220px;
  }
  .contact__name {
    color: var(--gold); font-weight: 800; font-size: 24px;
    text-transform: uppercase; line-height: 1;
  }
  .contact__role {
    color: #fff; font-weight: 700; font-size: 12px;
    letter-spacing: .5px; text-transform: uppercase; margin-top: 3px;
  }
  .rule { height: 2px; background: var(--gold); margin: 10px 0; }
  .social {
    display: flex; align-items: center; gap: 6px;
    color: var(--text); font-size: 12.5px; font-weight: 500;
  }
  .social__icon {
    width: 16px; height: 16px; border-radius: 50%; background: var(--gold);
  }
  .contact__lines {
    list-style: none; color: var(--text); font-size: 12.5px;
    font-weight: 500; line-height: 1.45;
  }

  .tagline-band {
    position: absolute; left: 0; right: 0; bottom: 0; height: 48px;
    background: linear-gradient(90deg, var(--amber) 0%, var(--sun) 100%);
    display: flex; align-items: center; justify-content: center;
    color: var(--ink); font-weight: 700; font-size: 16px;
  }

  /* Back services */
  .services {
    position: absolute; left: 330px; top: 70px;
    list-style: none;
  }
  .services__item {
    position: relative; padding-left: 16px;
    color: var(--text); font-size: 14px; font-weight: 600;
    line-height: 23px;
  }
  .services__item::before {
    content: ""; position: absolute; left: 0; top: 8px;
    width: 7px; height: 7px; border-radius: 50%; background: var(--gold);
  }
</style>
</head>
<body>
<main class="canvas">

  <section class="card card--front" aria-label="Business card front">
    <div class="brand">
      <span class="brand__dot" aria-hidden="true"></span>
      <span class="brand__name">Lucky<br>Harbour</span>
    </div>

    <div class="contact">
      <p class="contact__name">Rob Kendall</p>
      <p class="contact__role">Director</p>
      <div class="rule"></div>
      <div class="social">
        <span class="social__icon" aria-hidden="true"></span>
        <span class="social__icon" aria-hidden="true"></span>
        <span>@luckyharbourevents</span>
      </div>
      <div class="rule"></div>
      <ul class="contact__lines">
        <li>info@luckyharbour.com.au</li>
        <li>1300 482 617 &nbsp;|&nbsp; 0433 728 591</li>
        <li>www.luckyharbour.com.au</li>
      </ul>
    </div>

    <div class="tagline-band">Australia's #1 Fun Casino Specialists</div>
  </section>

  <section class="card card--back" aria-label="Business card back">
    <div class="brand">
      <span class="brand__dot" aria-hidden="true"></span>
      <span class="brand__name">Lucky<br>Harbour</span>
    </div>

    <ul class="services">
      <li class="services__item">Corporate Events</li>
      <li class="services__item">Private Parties</li>
      <li class="services__item">Poker Tournaments</li>
      <li class="services__item">Fundraising</li>
      <li class="services__item">Props &amp; Theming</li>
      <li class="services__item">Photo Booth</li>
      <li class="services__item">Horse Racing Events</li>
    </ul>
  </section>

</main>
</body>
</html>
```